Private chef located in Vail, CO

I would like my info located at the top of the landing page, perhaps some Vail mountain landscapes that I could swap out from summer to winter photos. I need the menu bar to have a link to a blog, about me, photo gallery, recipes & beer reviews. I would also like to have a shop, but only populated with products from corvelle or other online retailers that I can affiliate with.
Extremely wealthy, affluent people, concierge, international
5+ page

```html
<!DOCTYPE html>
<html lang="en">
<head>
<meta charset="utf-8">
<title>Marcus Holloway – Private Chef in Vail</title>
<link href="https://fonts.googleapis.com/css2?family=Montserrat:wght@400;500;600;700;800&family=Open+Sans:wght@400;600;700&family=Oswald:wght@600&display=swap" rel="stylesheet">
<style>
:root{
  --red:#d71920;
  --red-dark:#b3121a;
  --gold:#f2b21b;
  --ink:#1b1b1b;
  --text:#555;
  --muted:#777;
  --light:#efefef;
  --footer:#111;
  --white:#fff;
  --line:#e2e2e2;
}
*{margin:0;padding:0;box-sizing:border-box}
html,body{width:1200px;height:4276px;overflow:hidden}
body{position:relative;background:var(--white);font-family:"Open Sans",Arial,sans-serif;color:var(--text)}
.abs{position:absolute}
h2.section-title{position:absolute;left:0;width:1200px;text-align:center;font-family:"Montserrat",Arial,sans-serif;font-weight:500;font-size:44px;color:var(--ink)}
.section-sub{position:absolute;left:0;width:1200px;text-align:center;font-size:19px;color:#444}
.btn{display:inline-block;background:var(--red);color:var(--white);font-family:"Montserrat",Arial,sans-serif;font-weight:600;font-size:17px;padding:9px 24px;border-radius:5px;box-shadow:5px 0 0 var(--gold);text-decoration:none}

/* Hero */
.hero{left:0;top:0;width:1200px;height:700px;background:linear-gradient(180deg,#d9e4ee 0%,#b7c9db 30%,#5f7793 55%,#e8eef5 80%,#c7d3df 100%)}
.brand{left:86px;top:36px;font-family:"Oswald",Arial,sans-serif;font-size:36px;color:var(--ink);letter-spacing:.3px;white-space:nowrap}
.topbar{right:92px;top:30px;display:flex;align-items:center;gap:12px;font-size:20px;color:var(--ink)}
.search-dot{width:28px;height:28px;border-radius:50%;background:var(--gold);display:flex;align-items:center;justify-content:center}
.phone-dot{width:28px;height:28px;border-radius:50%;background:var(--red);display:flex;align-items:center;justify-content:center}
.nav{right:92px;top:78px;display:flex;gap:28px;font-family:"Montserrat",Arial,sans-serif;font-weight:500;font-size:15px;color:var(--ink);white-space:nowrap}
.hero-title{left:0;top:255px;width:1200px;text-align:center;font-family:"Montserrat",Arial,sans-serif;font-weight:800;font-size:74px;color:var(--white);text-shadow:0 3px 8px rgba(0,0,0,.35)}
.hero-tag{left:0;top:352px;width:1200px;text-align:center;font-family:"Montserrat",Arial,sans-serif;font-weight:600;font-size:30px;line-height:44px;color:var(--white);text-shadow:0 2px 6px rgba(0,0,0,.4)}
.slide-arrow{top:316px;width:30px;height:30px;border-radius:50%;background:rgba(0,0,0,.55);display:flex;align-items:center;justify-content:center}

/* Intro card */
.intro-card{left:86px;top:578px;width:1020px;height:328px;background:var(--white);box-shadow:0 4px 16px rgba(0,0,0,.18);display:flex}
.intro-photo{width:304px;height:100%;background:linear-gradient(135deg,#3a3532,#6b5a4a 55%,#2a2624)}
.intro-body{padding:30px 40px 0 40px}
.intro-body h3{font-family:"Montserrat",Arial,sans-serif;font-weight:500;font-size:33px;color:var(--ink)}
.intro-body .role{color:var(--red);font-size:20px;margin-top:6px}
.intro-body p{font-size:20px;line-height:31px;color:var(--text);margin:18px 0 22px;width:600px}

/* Services */
.services-line{left:208px;top:1217px;width:778px;border-top:2px dashed #e08a8a}
.service{width:240px;text-align:center}
.service .ring{width:100px;height:100px;border-radius:50%;border:3px solid #e6a3a3;background:var(--white);margin:0 auto;display:flex;align-items:center;justify-content:center;box-shadow:0 0 0 6px #f7e3e3}
.service.active .ring{background:var(--red);border-color:var(--red)}
.service h4{font-family:"Montserrat",Arial,sans-serif;font-weight:600;font-size:20px;color:var(--ink);margin-top:26px;letter-spacing:.3px}
.service.active h4{color:var(--red)}
.service p{font-size:16px;line-height:26px;color:var(--muted);margin-top:8px}

/* About */
.about-panel{left:0;top:1494px;width:638px;height:433px;background:var(--light)}
.about-panel h2{position:absolute;left:86px;top:60px;font-family:"Montserrat",Arial,sans-serif;font-weight:500;font-size:44px;color:var(--ink)}
.about-panel p{position:absolute;left:86px;top:132px;width:486px;font-size:15.5px;line-height:32px;color:var(--text);text-align:justify}
.about-panel .btn{position:absolute;left:86px;top:344px}
.about-photo{left:638px;top:1494px;width:562px;height:433px;background:linear-gradient(135deg,#1c1a18 0%,#3d3128 50%,#7a5b3d 75%,#1a1816 100%)}

/* Gallery */
.tile{width:326px;height:214px}

/* Reviews */
.reviews-band{left:0;top:2773px;width:1200px;height:294px;background:linear-gradient(135deg,var(--red-dark),var(--red) 60%,#c4151c)}
.reviews-band h2{position:absolute;left:0;top:64px;width:1200px;text-align:center;font-family:"Montserrat",Arial,sans-serif;font-weight:500;font-size:42px;color:var(--white)}
.review{top:2953px;width:453px;height:225px;background:var(--white);box-shadow:0 4px 14px rgba(0,0,0,.18);border-radius:4px}
.review .avatar{position:absolute;left:-36px;top:52px;width:120px;height:120px;border-radius:50%;background:linear-gradient(160deg,#6d6d6d,#2d2d2d);border:4px solid var(--white);box-shadow:0 2px 6px rgba(0,0,0,.2)}
.review .quote{position:absolute;right:36px;top:22px}
.review p{position:absolute;left:112px;top:76px;width:300px;font-size:15.5px;line-height:27px;color:var(--muted)}
.review .stars{position:absolute;left:112px;top:166px;display:flex;gap:2px}
.review .name{position:absolute;right:40px;top:160px;font-size:18px;color:#333}

/* Blog */
.blog-card{top:3431px;width:328px;height:345px;background:var(--white);box-shadow:0 4px 14px rgba(0,0,0,.16);text-align:center}
.blog-card .thumb{height:194px}
.blog-card .date{color:var(--red);font-size:14px;margin-top:16px}
.blog-card h5{font-family:"Montserrat",Arial,sans-serif;font-weight:600;font-size:17px;color:var(--ink);margin-top:12px}
.blog-card p{font-size:14px;line-height:22px;color:var(--muted);margin:8px auto 0;width:270px}
.blog-card .btn-sm{display:inline-block;margin-top:12px;background:var(--gold);color:#3a2a00;font-size:14px;padding:5px 22px;border-radius:3px}

/* Footer */
.footer-rule{left:0;top:3885px;width:1200px;height:8px;background:var(--red)}
.footer{left:0;top:3893px;width:1200px;height:383px;background:var(--footer);color:#ddd}
.footer h6{font-family:"Montserrat",Arial,sans-serif;font-weight:500;font-size:20px;color:var(--white);letter-spacing:.5px}
.footer .fbrand{position:absolute;left:86px;top:86px;font-family:"Oswald",Arial,sans-serif;font-size:30px;color:var(--white)}
.footer .fabout{position:absolute;left:86px;top:132px;width:300px;font-size:14px;line-height:22px;color:#ccc}
.footer .col{position:absolute;top:70px}
.footer ul{list-style:none;margin-top:30px}
.footer .contact li{display:flex;align-items:flex-start;gap:18px;font-size:14px;line-height:20px;margin-bottom:22px}
.footer .links li{font-size:14px;margin-bottom:10px;padding-left:18px;position:relative}
.footer .links li:before{content:"";position:absolute;left:0;top:8px;width:5px;height:5px;border-radius:50%;background:#ddd}
.footer .social li{display:flex;align-items:center;gap:12px;font-size:16px;margin-bottom:18px}
.footer .social .circle{width:26px;height:26px;border-radius:50%;border:1.5px solid #ddd}
.copyright{position:absolute;left:0;top:318px;width:1200px;text-align:center;font-size:15px;color:#ddd}
</style>
</head>
<body>

<!-- Header & hero -->
<section class="abs hero" role="img" aria-label="Snowy Vail mountain range under a blue sky"></section>
<div class="abs brand">MARCUS HOLLOWAY</div>
<div class="abs topbar">
  <span class="search-dot"><svg width="14" height="14" viewBox="0 0 14 14"><circle cx="6" cy="6" r="4" fill="none" stroke="#222" stroke-width="2"/><line x1="9" y1="9" x2="13" y2="13" stroke="#222" stroke-width="2"/></svg></span>
  <span class="phone-dot"><svg width="14" height="14" viewBox="0 0 24 24"><path d="M6.6 10.8a15 15 0 006.6 6.6l2.2-2.2c.3-.3.7-.4 1-.2 1.1.4 2.3.6 3.6.6.6 0 1 .4 1 1V20c0 .6-.4 1-1 1A17 17 0 013 4c0-.6.4-1 1-1h3.5c.6 0 1 .4 1 1 0 1.3.2 2.5.6 3.6.1.3 0 .7-.2 1z" fill="#fff"/></svg></span>
  <span>+1 970 555 0142</span>
</div>
<nav class="abs nav">
  <span>Home</span><span>Blog</span><span>About me</span><span>Photo gallery</span><span>Recipes &amp; Beer reviews</span><span>Contact us</span>
</nav>
<h1 class="abs hero-title">MARCUS HOLLOWAY</h1>
<div class="abs hero-tag">Innovative technique, attention to detail,<br>focus on exceeding the guests expectations.</div>
<div class="abs slide-arrow" style="left:54px"><svg width="12" height="12" viewBox="0 0 12 12"><path d="M8 1L3 6l5 5" stroke="#fff" stroke-width="2" fill="none"/></svg></div>
<div class="abs slide-arrow" style="left:1112px"><svg width="12" height="12" viewBox="0 0 12 12"><path d="M4 1l5 5-5 5" stroke="#fff" stroke-width="2" fill="none"/></svg></div>

<article class="abs intro-card">
  <div class="intro-photo" role="img" aria-label="The chef in a cap smiling beside a roast in the oven"></div>
  <div class="intro-body">
    <h3>Chef Marcus Holloway</h3>
    <div class="role">Private Chef in Vail</div>
    <p>I have been cooking my whole life, I spent my late 20's cooking for professional athletes, this led me to pursue cooking professionally. I have cooked through Central America, living in Costa Rica and Panama</p>
    <span class="btn">Read More</span>
  </div>
</article>

<!-- Services -->
<h2 class="section-title" style="top:1020px">My Services</h2>
<div class="section-sub" style="top:1082px">As a professional Chef, I offer the following services</div>
<div class="abs services-line"></div>
<div class="abs service" style="left:88px;top:1167px">
  <div class="ring"><svg width="46" height="46" viewBox="0 0 48 48" fill="none" stroke="var(--red)" stroke-width="2.5"><path d="M14 28c-5 0-8-4-8-8s4-8 8-7c1-4 5-7 10-7s9 3 10 7c4-1 8 3 8 7s-3 8-8 8"/><path d="M14 28v12h20V28"/><line x1="14" y1="34" x2="34" y2="34"/></svg></div>
  <h4>PERSONAL CHEF</h4>
</div>
<div class="abs service" style="left:342px;top:1167px">
  <div class="ring"><svg width="46" height="46" viewBox="0 0 48 48" fill="none" stroke="var(--red)" stroke-width="2.5"><rect x="6" y="10" width="36" height="32" rx="2"/><line x1="6" y1="18" x2="42" y2="18"/><line x1="14" y1="6" x2="14" y2="13"/><line x1="34" y1="6" x2="34" y2="13"/><path d="M13 24h4M22 24h4M31 24h4M13 30h4M22 30h4M31 30h4M13 36h4M22 36h4"/></svg></div>
  <h4>FULL-TIME CHEF</h4>
</div>
<div class="abs service active" style="left:601px;top:1167px">
  <div class="ring"><svg width="46" height="46" viewBox="0 0 48 48" fill="none" stroke="#fff" stroke-width="2.5" stroke-linecap="round"><path d="M10 40L32 18"/><path d="M30 8c4-2 10 4 8 8l-6 4-6-6z"/><path d="M38 40L16 18"/><path d="M10 8l8 8M14 6l6 6M8 12l6 6"/></svg></div>
  <h4>CATERING</h4>
  <p>I can provide catering services in Vail for weddings, birthdays, corporate events and more.</p>
</div>
<div class="abs service" style="left:866px;top:1167px">
  <div class="ring"><svg width="46" height="46" viewBox="0 0 48 48" fill="none" stroke="var(--red)" stroke-width="2.5"><path d="M24 44S10 30 10 19a14 14 0 0128 0c0 11-14 25-14 25z"/><path d="M20 14v8M24 14v8M28 14v8M20 22h8M24 22v10"/></svg></div>
  <h4>KEEPWELL MEALS</h4>
</div>

<!-- About -->
<section class="abs about-panel">
  <h2>Get to know me better</h2>
  <p>I have been cooking my whole life, I spent my late 20's cooking for professional athletes, this led me to pursue cooking professionally. I have cooked through Central America, living in Costa Rica and Panama. I have been based in Vail the past few years, taking a year hiatus to Chicago to work in some Aster Guide starred restaurants &amp; gain experience working for some incredible chefs.</p>
  <span class="btn">Read More</span>
</section>
<div class="abs about-photo" role="img" aria-label="Chef drizzling oil over a plated steak with herbs"></div>

<!-- Gallery -->
<h2 class="section-title" style="top:2058px">Gallery Marcus</h2>
<div class="section-sub" style="top:2120px">Here you can see some of my dishes and other pictures</div>
<div class="abs tile" style="left:94px;top:2197px;background:linear-gradient(135deg,#3b3a2c,#6d7a3a 50%,#b33a2a)" role="img" aria-label="Plated greens with red garnish"></div>
<div class="abs tile" style="left:437px;top:2197px;background:linear-gradient(135deg,#1d1a14,#c9b27a 50%,#2b2418)" role="img" aria-label="Ceviche in a dark bowl"></div>
<div class="abs tile" style="left:780px;top:2197px;background:linear-gradient(135deg,#2c2c3a,#a65a3c 50%,#e2b84a)" role="img" aria-label="Tartare topped with egg yolk and flowers"></div>
<div class="abs tile" style="left:94px;top:2431px;background:linear-gradient(135deg,#5a1c14,#8a2a1c 50%,#3a1a12)" role="img" aria-label="Grilled steak with char marks"></div>
<div class="abs tile" style="left:437px;top:2431px;background:linear-gradient(135deg,#1a1714,#7a5632 50%,#d8c9a8)" role="img" aria-label="Fried eggs in a skillet"></div>
<div class="abs tile" style="left:780px;top:2431px;background:linear-gradient(135deg,#3a3326,#8a7a52 50%,#f0ece2)" role="img" aria-label="Plated dish with cream and greens"></div>

<!-- Reviews -->
<section class="abs reviews-band" role="img" aria-label="Red toned food backdrop"><h2>Reviews</h2></section>
<div class="abs review" style="left:131px">
  <div class="avatar" role="img" aria-label="Reviewer portrait"></div>
  <svg class="quote" width="46" height="36" viewBox="0 0 46 36"><path d="M0 36V20C0 9 6 2 16 0l2 5c-6 2-9 6-9 11h9v20zM26 36V20C26 9 32 2 42 0l2 5c-6 2-9 6-9 11h9v20z" fill="var(--gold)"/></svg>
  <p>The point of using Lorem Ipsum is that it has a more-or-less normal distribution of letters, as opposed to using 'Content</p>
  <div class="stars"><svg width="88" height="16" viewBox="0 0 88 16" fill="var(--gold)"><path id="st" d="M8 0l2.4 5 5.6.8-4 3.9.9 5.5L8 12.6 3.1 15.2l.9-5.5-4-3.9L5.6 5z"/><use href="#st" x="18"/><use href="#st" x="36"/><use href="#st" x="54"/><use href="#st" x="72"/></svg></div>
  <div class="name">- &nbsp;Helen</div>
</div>
<div class="abs review" style="left:653px">
  <div class="avatar" role="img" aria-label="Reviewer portrait"></div>
  <svg class="quote" width="46" height="36" viewBox="0 0 46 36"><path d="M0 36V20C0 9 6 2 16 0l2 5c-6 2-9 6-9 11h9v20zM26 36V20C26 9 32 2 42 0l2 5c-6 2-9 6-9 11h9v20z" fill="var(--gold)"/></svg>
  <p>The point of using Lorem Ipsum is that it has a more-or-less normal distribution of letters, as opposed to using 'Content</p>
  <div class="stars"><svg width="88" height="16" viewBox="0 0 88 16" fill="var(--gold)"><use href="#st"/><use href="#st" x="18"/><use href="#st" x="36"/><use href="#st" x="54"/><use href="#st" x="72"/></svg></div>
  <div class="name">- Amet</div>
</div>
<svg class="abs" style="left:140px;top:3198px" width="30" height="22" viewBox="0 0 30 22"><path d="M29 11H3M11 2L2 11l9 9" stroke="#111" stroke-width="2.5" fill="none"/></svg>
<svg class="abs" style="left:1070px;top:3198px" width="30" height="22" viewBox="0 0 30 22"><path d="M1 11h26M19 2l9 9-9 9" stroke="#111" stroke-width="2.5" fill="none"/></svg>

<!-- Blog -->
<h2 class="section-title" style="top:3326px">Latest Blog</h2>
<article class="abs blog-card" style="left:80px">
  <div class="thumb" style="background:linear-gradient(135deg,#6a2a1c,#b0604a 50%,#4a2a1e)" role="img" aria-label="Sliced grilled steak"></div>
  <div class="date">JAN 25,2019</div>
  <h5>Dolorem ipsum quia dolor</h5>
  <p>It has survived not only five centuries, but also the leap into electronic</p>
  <span class="btn-sm">Read More</span>
</article>
<article class="abs blog-card" style="left:436px">
  <div class="thumb" style="background:linear-gradient(135deg,#141414,#9a3a1a 50%,#1a1a1a)" role="img" aria-label="Chef flaming a pan"></div>
  <div class="date">JAN 25,2019</div>
  <h5>Dolorem ipsum quia dolor</h5>
  <p>It has survived not only five centuries, but also the leap into electronic</p>
  <span class="btn-sm">Read More</span>
</article>
<article class="abs blog-card" style="left:792px">
  <div class="thumb" style="background:linear-gradient(135deg,#2a2a2a,#8a5a3a 50%,#3a2a20)" role="img" aria-label="Meat roasting on skewers"></div>
  <div class="date">JAN 25,2019</div>
  <h5>Dolorem ipsum quia dolor</h5>
  <p>It has survived not only five centuries, but also the leap into electronic</p>
  <span class="btn-sm">Read More</span>
</article>

<!-- Footer -->
<div class="abs footer-rule"></div>
<footer class="abs footer">
  <div class="fbrand">MARCUS HOLLOWAY</div>
  <p class="fabout">It is a long established fact that a reader will be distracted by the readable content of a page when looking at its layout</p>
  <svg class="abs" style="left:86px;top:214px" width="24" height="14" viewBox="0 0 24 14"><path d="M0 7h21M15 1l6 6-6 6" stroke="var(--red)" stroke-width="2.5" fill="none"/></svg>

  <div class="col" style="left:465px">
    <h6>CONTACT US</h6>
    <ul class="contact">
      <li><svg width="16" height="20" viewBox="0 0 16 20"><path d="M8 20S1 12 1 7.5a7 7 0 0114 0C15 12 8 20 8 20z" fill="#fff"/><circle cx="8" cy="7.5" r="2.5" fill="#111"/></svg><span>418 Alpine Meadow Rd #12<br>Vail, CO 81657</span></li>
      <li><svg width="16" height="16" viewBox="0 0 24 24"><path d="M6.6 10.8a15 15 0 006.6 6.6l2.2-2.2c.3-.3.7-.4 1-.2 1.1.4 2.3.6 3.6.6.6 0 1 .4 1 1V20c0 .6-.4 1-1 1A17 17 0 013 4c0-.6.4-1 1-1h3.5c.6 0 1 .4 1 1 0 1.3.2 2.5.6 3.6.1.3 0 .7-.2 1z" fill="#fff"/></svg><span>970.555.0187</span></li>
      <li><svg width="16" height="14" viewBox="0 0 16 14"><rect x="0" y="1" width="16" height="12" rx="1" fill="#fff"/><path d="M0 2l8 6 8-6" stroke="#111" stroke-width="1.5" fill="none"/></svg><span>hello@hollowaychef.com</span></li>
    </ul>
  </div>

  <div class="col" style="left:795px">
    <h6>QUICK LINKS</h6>
    <ul class="links">
      <li>Home</li><li>About us</li><li>Reviews</li><li>Blog</li><li>Sitemap</li>
    </ul>
  </div>

  <div class="col" style="left:1002px">
    <h6>FOLLOW US</h6>
    <ul class="social">
      <li><span class="circle"></span>Pinefeed</li>
      <li><span class="circle"></span>Snapframe</li>
      <li><span class="circle"></span>Circleplus</li>
    </ul>
  </div>

  <div class="copyright">© Copyright 2019 . All Rights Reserved.</div>
</footer>

</body>
</html>
```